Australian Trucking Company Requires Professional Looking Stationary

We require a professional looking stationary design that incorporates our newly designed logo.

Our business, called "Brell Haulage Contracting", provides contracting work, transport and logistics to business in Western Australia particularly with links to the mining sector.

We are a small business looking to expand and our new logo and our new stationary will help develop our brand image in our market place.

Target Market(s)

Businesses and Corporation with links to the Mining Sector

Industry/Entity Type

Small Business

Requirements
Must have
• The letterhead must have the following details:
The new logo

Text saying: "Brell Holdings Pty Ltd (ACN 582 316 907) ATF The Brell Discretionary Trust T/AS"
"ABN 71 834 209 553"
Address "P.O Box 817 Wattlegrove WA, 6958"
Phone: 08 9352 7140
Email: brellhaul@mailbox-example.com.au

The text on the letterhead should be editable as the details are likely to change in the near future. Provision should be made for a website address all though one isn't available at the moment.

The styling, layout and font text is entirely up to the designer.

```html
<!DOCTYPE html>
<html lang="en">
<head>
<meta charset="utf-8">
<title>Brell Haulage Contracting – Business Cards</title>
<link rel="stylesheet" href="https://fonts.googleapis.com/css2?family=Arimo:wght@400;700&display=swap">
<style>
  :root {
    --page: #e9e6e2;
    --card: #ffffff;
    --brand-red: #b3121e;
    --accent-red: #e2202c;
    --rule: #b86a70;
    --ink: #555555;
    --ink-soft: #6a6a6a;
    --ink-faint: #b5b5b5;
  }
  * { box-sizing: border-box; margin: 0; padding: 0; }
  html, body {
    width: 1200px; height: 665px; overflow: hidden;
    background: var(--page);
    font-family: "Arimo", Arial, sans-serif;
  }
  .sheet {
    position: relative; width: 1200px; height: 665px;
    display: flex; justify-content: center; align-items: center; gap: 60px;
  }
  .card {
    position: relative; width: 520px; height: 297px;
    background: var(--card);
    box-shadow: 0 2px 10px rgba(0,0,0,0.12);
  }

  /* brand name set as plain text */
  .brand-name {
    color: var(--brand-red);
    font-weight: 700;
    text-transform: uppercase;
    line-height: 1.02;
    letter-spacing: 0.5px;
  }
  .brand-dot {
    display: inline-block; border-radius: 50%;
    background: var(--brand-red);
  }

  /* front: contact side */
  .card--contact .brand {
    position: absolute; left: 30px; top: 40px;
    display: flex; align-items: center; gap: 12px;
  }
  .card--contact .brand-dot { width: 14px; height: 14px; }
  .card--contact .brand-name { font-size: 19px; }
  .card--contact .rule {
    position: absolute; left: 0; right: 0; top: 106px; height: 1px;
    background: var(--rule);
  }
  .holder {
    position: absolute; right: 32px; top: 30px; text-align: right;
    background: var(--card); padding-left: 10px;
  }
  .holder-name { font-size: 17px; font-weight: 700; color: var(--ink); }
  .holder-title { font-size: 11px; color: var(--ink-soft); margin-top: 2px; }
  .contact-list {
    position: absolute; right: 32px; top: 128px;
    list-style: none; text-align: right;
    font-size: 12px; color: var(--ink-soft);
  }
  .contact-list li {
    display: flex; justify-content: flex-end; align-items: center; gap: 6px;
    margin-bottom: 11px;
  }
  .contact-list .address { display: block; line-height: 1.35; }
  .contact-list svg { width: 11px; height: 11px; flex: none; }
  .abn {
    position: absolute; right: 32px; bottom: 42px;
    font-size: 11.5px; color: var(--ink-faint);
  }

  /* back: brand side */
  .card--brand .brand {
    position: absolute; left: 0; right: 0; top: 90px;
    display: flex; justify-content: center; align-items: center; gap: 18px;
  }
  .card--brand .brand-dot { width: 22px; height: 22px; }
  .card--brand .brand-name { font-size: 34px; }
  .web {
    position: absolute; left: 0; right: 0; bottom: 40px; text-align: center;
    font-size: 13px; letter-spacing: 0.5px;
  }
  .web .web-part { color: var(--accent-red); }
  .web .web-domain { color: var(--ink); font-weight: 700; font-size: 14px; }
</style>
</head>
<body>
<main class="sheet">

  <section class="card card--contact" aria-label="Business card, contact side">
    <div class="rule"></div>
    <div class="brand">
      <span class="brand-dot"></span>
      <div class="brand-name">Brell<br>Haulage<br>Contracting</div>
    </div>
    <div class="holder">
      <p class="holder-name">Name here</p>
      <p class="holder-title">Title</p>
    </div>
    <ul class="contact-list">
      <li>08 9352 7140
        <svg viewBox="0 0 12 12" aria-hidden="true"><circle cx="6" cy="6" r="5.2" fill="none" stroke="#e2202c" stroke-width="1.2"/><path d="M4.2 3.2 L5.2 3 L5.6 4.6 L5 5 Q5.6 6.6 7 7 L7.4 6.4 L9 6.8 L8.8 7.8 Q6.8 9 4.4 6.8 Q3 4.8 4.2 3.2Z" fill="#e2202c"/></svg>
      </li>
      <li>brellhaul@mailbox-example.com.au
        <svg viewBox="0 0 12 12" aria-hidden="true"><rect x="1" y="2.5" width="10" height="7" fill="#e2202c"/><path d="M1 2.8 L6 6.6 L11 2.8" fill="none" stroke="#fff" stroke-width="1"/></svg>
      </li>
      <li>www.brellhaul-example.com
        <svg viewBox="0 0 12 12" aria-hidden="true"><circle cx="6" cy="6" r="5" fill="none" stroke="#e2202c" stroke-width="1.2"/><ellipse cx="6" cy="6" rx="2.2" ry="5" fill="none" stroke="#e2202c" stroke-width="1"/><path d="M1 6 H11" stroke="#e2202c" stroke-width="1"/></svg>
      </li>
      <li><span class="address">P.O Box 817 Wattlegrove WA,<br>6958</span></li>
    </ul>
    <p class="abn">ABN 71 834 209 553</p>
  </section>

  <section class="card card--brand" aria-label="Business card, brand side">
    <div class="brand">
      <span class="brand-dot"></span>
      <div class="brand-name">Brell<br>Haulage<br>Contracting</div>
    </div>
    <p class="web"><span class="web-part">www.</span><span class="web-domain">brellhaul-example</span><span class="web-part">.com</span></p>
  </section>

</main>
</body>
</html>
```